Web design project for exciting Australian start-up

Background
We are looking for a creative and talented web design artist to work alongside our market leading web developer.
• You will be required to create a modern and clean design theme for our website, incorporating selected rustic colour scheme elements for our exciting Australian start-up to operate within the coffee industry.
reoccurring work to be expected to flow to the successful designer.
Requirements
• c. 5 - 10 page website
• Landing page
• Log in/ out
• 404 template
• Typography is emphasised
• Please use either a) typemarrow.com, b) free web fonts, c) brindle fonts
• All design elements in vector format
• Preferably with icons for each header title(i.e. about us, how it works etc) but designer have free reign over how the site looks, so might not be applicable
• All pages to be responsive
• Down to eSlab resolution

High level visual design brief attached - additional pages to be worked from base design.

Design inspiration
• We would like to use design elements from the following sources:
http://www.zandrix.com/halcyon/ (Functionality)
Colour scheme refer to logo and complementary style guide

```html
<!DOCTYPE html>
<html lang="en">
<head>
<meta charset="utf-8">
<title>Brewline — Online Coffee Market Place</title>
<link rel="stylesheet" href="https://fonts.googleapis.com/css2?family=Oswald:wght@500;700&family=Roboto:wght@300;400&family=Lato:wght@300;400&display=swap">
<style>
  :root{
    --orange:#f7913a;
    --orange-deep:#f2780f;
    --red:#ea3340;
    --ink:#2b2b2b;
    --grey-text:#555;
    --grey-line:#c9c9c9;
    --footer-bg:#e8e8e8;
    --white:#fff;
    --photo-light:#eeece9;
    --photo-mid:#d8cfc6;
    --coffee-mid:#7a3a1f;
    --coffee-dark:#3b1c10;
  }
  *{box-sizing:border-box;margin:0;padding:0}
  html,body{width:1200px;height:988px;overflow:hidden;background:var(--white)}
  body{position:relative;font-family:"Roboto",Helvetica,Arial,sans-serif;color:var(--ink)}

  .site-header{position:absolute;left:0;top:0;width:1200px;height:98px;background:var(--white)}
  .nav-btn{position:absolute;top:33px;height:29px;display:flex;align-items:center;justify-content:center;
    font-size:13px;text-transform:uppercase;border:1px solid var(--grey-line);background:#f6f6f6;color:#444;text-decoration:none;border-radius:1px}
  .nav-btn--home{left:52px;width:86px;background:var(--orange);border-color:var(--orange);color:var(--white)}
  .nav-btn--about{left:147px;width:85px}
  .nav-btn--how{left:942px;width:113px}
  .nav-btn--login{left:1065px;width:84px;background:var(--red);border-color:var(--red);color:var(--white);gap:6px}
  .brand{position:absolute;left:0;width:1200px;top:22px;display:flex;justify-content:center;align-items:center;gap:10px}
  .brand-mark{width:46px;height:46px;border-radius:50%;background:var(--orange)}
  .brand-name{font-family:"Oswald",sans-serif;font-weight:700;font-size:36px;letter-spacing:4px;color:var(--ink)}

  .hero{position:absolute;left:0;top:98px;width:1200px;height:691px;overflow:hidden}
  .hero-photo{position:absolute;inset:0;background:linear-gradient(180deg,var(--photo-light) 0%,var(--photo-mid) 62%,var(--coffee-mid) 80%,var(--coffee-dark) 100%)}
  .hero-copy{position:absolute;left:69px;top:140px}
  .hero-kicker{font-weight:400;font-size:53px;letter-spacing:-2.6px;color:#3d3d3d;line-height:52px}
  .hero-title{font-family:"Oswald",sans-serif;font-weight:700;font-size:72px;line-height:74px;color:var(--red);letter-spacing:2.2px}
  .hero-sub{font-family:"Oswald",sans-serif;font-weight:700;font-size:60px;line-height:62px;color:var(--orange-deep);letter-spacing:0}
  .watch-btn{position:absolute;left:69px;top:347px;width:189px;height:43px;border:1px solid #9a9a9a;background:rgba(255,255,255,.35);
    display:flex;align-items:center;gap:16px;padding-left:24px;font-family:"Oswald",sans-serif;font-weight:500;font-size:20px;color:#333;text-decoration:none}

  .site-footer{position:absolute;left:0;top:789px;width:1200px;height:199px;background:var(--footer-bg);overflow:hidden;font-family:"Lato",sans-serif}
  .footer-ring{position:absolute;left:875px;top:2px;width:290px;height:290px;border-radius:50%;border:6px solid rgba(0,0,0,.035)}
  .footer-col{position:absolute;top:35px}
  .footer-heading{font-family:"Roboto",sans-serif;font-weight:400;font-size:14px;color:#111;text-transform:uppercase;margin-bottom:12px}
  .footer-about{left:51px;width:305px}
  .footer-about p{font-size:12px;font-weight:300;line-height:16.6px;color:#444}
  .footer-links{list-style:none}
  .footer-links li{font-size:13.5px;font-weight:300;color:#222;line-height:20.4px}
  .col-info{left:429px}
  .col-who{left:618px}
  .col-follow{left:788px}
  .social li{display:flex;align-items:center;gap:9px;font-size:14.5px;line-height:27px;color:#444}
  .social-dot{width:17px;height:17px;border-radius:50%;background:#9b9b9b}
  .footer-brand{position:absolute;left:962px;top:62px;display:flex;align-items:center;gap:8px}
  .footer-brand .brand-mark{width:34px;height:34px;background:#b5b5b5}
  .footer-brand .brand-name{font-size:22px;color:#555;letter-spacing:2px}
  .copyright{position:absolute;left:962px;top:117px;font-size:13.5px;font-weight:300;color:#333}
</style>
</head>
<body>
  <header class="site-header">
    <a class="nav-btn nav-btn--home" href="#">Home</a>
    <a class="nav-btn nav-btn--about" href="#">About Us</a>
    <div class="brand"><span class="brand-mark"></span><span class="brand-name">BREWLINE</span></div>
    <a class="nav-btn nav-btn--how" href="#">How It Works</a>
    <a class="nav-btn nav-btn--login" href="#">
      <svg width="13" height="14" viewBox="0 0 13 14" aria-hidden="true"><circle cx="6.5" cy="4" r="3.5" fill="#fff"/><path d="M0 14c0-4 3-6 6.5-6S13 10 13 14z" fill="#fff"/></svg>
      Login
    </a>
  </header>

  <section class="hero">
    <div class="hero-photo" role="img" aria-label="Banner photo: soft-focus cafe scene with a cup of espresso on a saucer and a heap of roasted coffee beans along the bottom"></div>
    <div class="hero-copy">
      <div class="hero-kicker">AUSTRALIA’S FIRST</div>
      <div class="hero-title">ONLINE COFFEE</div>
      <div class="hero-sub">MARKET PLACE</div>
    </div>
    <a class="watch-btn" href="#">
      <svg width="13" height="15" viewBox="0 0 13 15" aria-hidden="true"><path d="M0 0L13 7.5L0 15z" fill="var(--red)"/></svg>
      WATCH VIDEO
    </a>
  </section>

  <footer class="site-footer">
    <div class="footer-ring"></div>
    <div class="footer-col footer-about">
      <h3 class="footer-heading">About Us</h3>
      <p>Lorem ipsum dolor sit amet, consectetur adipisicing elit, sed do eiusmod tempor incididunt ut labore et dolore magna aliqua. Ut enim ad minim veniam, quis nostrud exercitation ullamco laboris nisi ut aliquip ex ea commodo consequat. Duis aute irure dolor in reprehenderit in voluptate velit esse cillum dolore eu fugiat nulla pariatur.</p>
    </div>
    <div class="footer-col col-info">
      <h3 class="footer-heading">Helpful Info</h3>
      <ul class="footer-links"><li>About us</li><li>Media Enquiries</li><li>Terms &amp; Conditions</li><li>Privacy Policy</li></ul>
    </div>
    <div class="footer-col col-who">
      <h3 class="footer-heading">Who We Are</h3>
      <ul class="footer-links"><li>How It Works</li><li>Faq</li><li>Contact Us</li></ul>
    </div>
    <div class="footer-col col-follow">
      <h3 class="footer-heading" style="margin-bottom:4px">Follow Us</h3>
      <ul class="footer-links social">
        <li><span class="social-dot"></span>Pagebook</li>
        <li><span class="social-dot"></span>Worklink</li>
        <li><span class="social-dot"></span>Pagebook</li>
        <li><span class="social-dot"></span>Worklink</li>
      </ul>
    </div>
    <div class="footer-brand"><span class="brand-mark"></span><span class="brand-name">BREWLINE</span></div>
    <div class="copyright">Copyright © 2014 Brewline.</div>
  </footer>
</body>
</html>
```